IT Company requires new Business Card design.

Over the years we have had a few different business card designs. We are now due for new cards across the board for all staff. We felt this would be a good time to start fresh with a new design. Our traditional card simply had our details on the front, and a list of services on the back. We don't particularly need the list of services, we have had cards where the only thing on the rear of the card was our logo.
Feel free to be creative, we would like our tag line "Managed IT Solutions" to appear at some point, doesn't necessarily have to be with the logo.
I have attached samples and drafts of various previous cards we have used over the years.

```html
<!DOCTYPE html>
<html lang="en">
<head>
<meta charset="utf-8">
<title>Corvale Systems – Business Card</title>
<link rel="stylesheet" href="https://fonts.googleapis.com/css2?family=Source+Sans+3:wght@400;600;700&display=swap">
<style>
  :root {
    --backdrop: #e6e7e8;
    --card: #ffffff;
    --slate: #5e6c76;
    --slate-light: #b4bcc2;
    --ink: #4f5961;
    --rule: #c9cdd0;
    --white: #ffffff;
  }
  * { margin: 0; padding: 0; box-sizing: border-box; }
  html, body {
    width: 1034px; height: 1200px; overflow: hidden;
    background: var(--backdrop);
    font-family: "Source Sans 3", "Helvetica Neue", Arial, sans-serif;
    color: var(--ink);
  }
  .canvas { position: relative; width: 1034px; height: 1200px; }
  .card {
    position: absolute; left: 75px; width: 902px; height: 518px;
    background: var(--card); border-radius: 34px; overflow: hidden;
    box-shadow: 0 2px 10px rgba(0,0,0,0.12);
  }
  .card--front { top: 62px; }
  .card--back { top: 631px; }

  .brand { position: absolute; left: 70px; top: 180px; width: 370px; }
  .brand__name {
    font-weight: 700; font-size: 40px; line-height: 1.1;
    color: var(--slate);
  }
  .brand__tagline {
    margin-top: 8px; font-size: 15px; font-weight: 600;
    letter-spacing: 3px; text-transform: uppercase; color: var(--slate);
  }

  .divider {
    position: absolute; left: 457px; top: 89px; width: 2px; height: 247px;
    background: var(--rule);
  }
  .person { position: absolute; left: 481px; top: 88px; }
  .person__name { font-size: 28px; font-weight: 700; color: var(--slate); line-height: 1.1; }
  .person__role { font-size: 22px; color: var(--ink); margin-top: 2px; }

  .contacts { position: absolute; left: 481px; top: 167px; list-style: none; }
  .contacts li {
    display: flex; align-items: center; height: 35px;
    font-size: 20px; color: var(--ink);
  }
  .contacts svg { width: 18px; height: 18px; margin-right: 12px; fill: var(--slate); flex: none; }

  .footer-rule {
    position: absolute; left: 0; right: 0; top: 392px; height: 2px;
    background: var(--slate-light);
  }
  .footer-band {
    position: absolute; left: 0; right: 0; bottom: 0; height: 110px;
    background: var(--slate);
  }
  .address {
    position: absolute; left: 72px; top: 432px;
    color: var(--white); font-size: 22px; line-height: 34px; font-style: normal;
  }

  .back-brand {
    position: absolute; left: 0; right: 0; top: 200px; text-align: center;
  }
  .back-brand__name {
    font-weight: 700; font-size: 64px; line-height: 1.0; color: var(--slate);
  }
  .back-brand__tagline {
    margin-top: 16px; font-size: 18px; font-weight: 600;
    letter-spacing: 4px; text-transform: uppercase; color: var(--slate);
  }
  .back-url {
    position: absolute; left: 0; right: 0; top: 462px; text-align: center;
    font-size: 25px; letter-spacing: 2px; color: var(--ink);
  }
</style>
</head>
<body>
<main class="canvas">
  <section class="card card--front">
    <div class="brand">
      <div class="brand__name">Corvale Systems</div>
      <div class="brand__tagline">Managed IT Solutions</div>
    </div>

    <div class="divider"></div>

    <div class="person">
      <div class="person__name">Marcus Hale</div>
      <div class="person__role">Operation Manager</div>
    </div>

    <ul class="contacts">
      <li><svg viewBox="0 0 24 24"><path d="M6.6 10.8c1.4 2.8 3.8 5.1 6.6 6.6l2.2-2.2c.3-.3.7-.4 1-.2 1.1.4 2.3.6 3.6.6.6 0 1 .4 1 1V20c0 .6-.4 1-1 1C10.6 21 3 13.4 3 4c0-.6.4-1 1-1h3.5c.6 0 1 .4 1 1 0 1.3.2 2.5.6 3.6.1.3 0 .7-.2 1z"/></svg>08 9356 4180</li>
      <li><svg viewBox="0 0 24 24"><path d="M7 1h10a2 2 0 0 1 2 2v18a2 2 0 0 1-2 2H7a2 2 0 0 1-2-2V3a2 2 0 0 1 2-2zm0 3v14h10V4zm5 15.5a1.2 1.2 0 1 0 0 2.4 1.2 1.2 0 0 0 0-2.4z"/></svg>0412 708 936</li>
      <li><svg viewBox="0 0 24 24"><path d="M7 2h10v6H7zM3 9h18a1 1 0 0 1 1 1v8a1 1 0 0 1-1 1h-3v3H6v-3H3a1 1 0 0 1-1-1v-8a1 1 0 0 1 1-1zm5 7v4h8v-4z"/></svg>08 9356 4180</li>
      <li><svg viewBox="0 0 24 24"><path d="M2 5h20v14H2zm2 2v.5l8 5 8-5V7zm0 2.8V17h16V9.8l-8 5z"/></svg>marcus@corvalesystems.com.au</li>
      <li><svg viewBox="0 0 24 24"><path d="M12 2a10 10 0 1 0 0 20 10 10 0 0 0 0-20zm6.9 9h-3a15 15 0 0 0-1.3-6 8 8 0 0 1 4.3 6zM12 4.1c.9 1.3 1.8 3.7 1.9 6.9h-3.8c.1-3.2 1-5.6 1.9-6.9zM9.4 5a15 15 0 0 0-1.3 6h-3a8 8 0 0 1 4.3-6zM5.1 13h3a15 15 0 0 0 1.3 6 8 8 0 0 1-4.3-6zm6.9 6.9c-.9-1.3-1.8-3.7-1.9-6.9h3.8c-.1 3.2-1 5.6-1.9 6.9zm2.6-.9a15 15 0 0 0 1.3-6h3a8 8 0 0 1-4.3 6z"/></svg>www.corvalesystems.com.au</li>
    </ul>

    <div class="footer-rule"></div>
    <div class="footer-band"></div>
    <address class="address">
      Unit 7 22 Harbour Road<br>Canning Vale WA 6155
    </address>
  </section>

  <section class="card card--back">
    <div class="back-brand">
      <div class="back-brand__name">Corvale Systems</div>
      <div class="back-brand__tagline">Managed IT Solutions</div>
    </div>
    <div class="back-url">www.corvalesystems.com.au</div>
  </section>
</main>
</body>
</html>
```